Accountability Project Graphics

I want to create 10 social media graphics (new Instagram size 4:5 (1080 x 1350 pixels) focusing on our Quilvo Accountability App, using any of the 3 pictures attached. Use the attached pics only, NO RANDOM STOCK PHOTOGRAPHY. For the color scheme, use the landing page colors/fonts (attached).
You can add any of the 3 photos attached but I mainly need BOLD text that includes these headlines and sub-headlines on them.
Please NOTE for all the headlines below, also add this sub-headline on each graphic:
Stay Consistent with RT in Your Pocket!
Here are the headlines:
• Stop Starting Over Every Monday
• You don't need more willpower. You need more support
• Built for women who are tired of doing this alone
• When Motivation Fades, RT Checks In
• The Support System You've Been Missing
• Support When Motivation Disappears
• What if RT Checked in Every Day?
• The Missing Piece Isn't Another Diet
• Eat the food you love. Stay accountable every day.
• One Bad Meal Doesn't Mean You Failed
women over 40 trying to lose weight

```html
<!DOCTYPE html>
<html lang="en">
<head>
<meta charset="utf-8">
<title>Accountability App Social Graphics</title>
<link rel="stylesheet" href="https://fonts.googleapis.com/css2?family=Gelasio:wght@700&display=swap">
<style>
  :root {
    --page: #ffffff;
    --card-edge: #f6d3de;
    --card-glow: #fbedf1;
    --ink: #111111;
    --accent: #d4507c;
    --portrait-dark: #1c2336;
    --portrait-mid: #2a3350;
  }
  * { margin: 0; padding: 0; box-sizing: border-box; }
  html, body {
    width: 1200px; height: 1199px; overflow: hidden;
    background: var(--page);
  }
  .sheet { position: relative; width: 1200px; height: 1199px; }
  .post {
    position: absolute;
    width: 271px; height: 340px;
    overflow: hidden;
    background: radial-gradient(ellipse at 45% 55%, var(--card-glow) 0%, var(--card-edge) 95%);
    font-family: "Gelasio", Georgia, serif;
    font-weight: 700;
  }
  .portrait {
    position: absolute;
    left: 194px; top: 8px;
    width: 77px; height: 332px;
    border-radius: 38px 38px 0 0;
    background: linear-gradient(180deg, var(--portrait-mid) 0%, var(--portrait-dark) 60%, var(--portrait-dark) 100%);
  }
  .copy {
    position: absolute;
    left: 15px;
    z-index: 2;
    white-space: nowrap;
  }
  .lead {
    color: var(--ink);
    font-size: 22px;
    line-height: 25px;
  }
  .lead.tight { line-height: 24px; }
  .punch {
    color: var(--accent);
    font-size: 25px;
    line-height: 31px;
    text-transform: uppercase;
    margin-top: 3px;
  }
  .tagline {
    position: absolute;
    left: 15px; bottom: 12px;
    width: 172px;
    z-index: 2;
    color: var(--ink);
    font-size: 12px;
    line-height: 15px;
  }
</style>
</head>
<body>
<main class="sheet">

  <section class="post" style="left:27px; top:69px;">
    <div class="portrait" role="img" aria-label="Smiling coach in black outfit, hand on hip"></div>
    <div class="copy" style="top:118px;">
      <p class="lead">Stop<br>Starting</p>
      <p class="punch">Over<br>Every<br>Monday</p>
    </div>
    <p class="tagline">Stay Consistent with RT in Your Pocket!</p>
  </section>

  <section class="post" style="left:319px; top:69px;">
    <div class="portrait" role="img" aria-label="Smiling coach in black outfit, hand on hip"></div>
    <div class="copy" style="top:66px;">
      <p class="lead tight">You don&#39;t<br>need more<br>willpower.</p>
      <p class="punch">You<br>need<br>more<br>support</p>
    </div>
    <p class="tagline">Stay Consistent with RT in Your Pocket!</p>
  </section>

  <section class="post" style="left:609px; top:69px;">
    <div class="portrait" role="img" aria-label="Smiling coach in black outfit, hand on hip"></div>
    <div class="copy" style="top:68px; left:23px;">
      <p class="lead tight">Built for<br>women<br>who are<br>tired of</p>
      <p class="punch">Doing<br>this<br>alone</p>
    </div>
    <p class="tagline" style="left:23px;">Stay Consistent with RT in Your Pocket!</p>
  </section>

  <section class="post" style="left:901px; top:69px;">
    <div class="portrait" role="img" aria-label="Smiling coach in black outfit, hand on hip"></div>
    <div class="copy" style="top:116px;">
      <p class="lead">When<br>Motivation</p>
      <p class="punch">Fades,<br>RT<br>checks in</p>
    </div>
    <p class="tagline">Stay Consistent with RT in Your Pocket!</p>
  </section>

  <section class="post" style="left:27px; top:430px;">
    <div class="portrait" role="img" aria-label="Smiling coach in black outfit, hand on hip"></div>
    <div class="copy" style="top:86px; left:25px;">
      <p class="lead">The<br>Support<br>System</p>
      <p class="punch">You&#39;ve<br>been<br>missing</p>
    </div>
    <p class="tagline" style="left:25px;">Stay Consistent with RT in Your Pocket!</p>
  </section>

  <section class="post" style="left:319px; top:430px;">
    <div class="portrait" role="img" aria-label="Smiling coach in black outfit, hand on hip"></div>
    <div class="copy" style="top:86px; left:25px;">
      <p class="lead">Support<br>When</p>
      <p class="punch">Moti-<br>vation<br>disap-<br>pears</p>
    </div>
    <p class="tagline" style="left:25px;">Stay Consistent with RT in Your Pocket!</p>
  </section>

  <section class="post" style="left:609px; top:430px;">
    <div class="portrait" role="img" aria-label="Smiling coach in black outfit, hand on hip"></div>
    <div class="copy" style="top:86px;">
      <p class="lead">What<br>if RT</p>
      <p class="punch">Checked<br>in<br>every<br>day?</p>
    </div>
    <p class="tagline">Stay Consistent with RT in Your Pocket!</p>
  </section>

  <section class="post" style="left:901px; top:430px;">
    <div class="portrait" role="img" aria-label="Smiling coach in black outfit, hand on hip"></div>
    <div class="copy" style="top:58px;">
      <p class="lead">The<br>Missing<br>Piece</p>
      <p class="punch">Isn&#39;t<br>another<br>diet</p>
    </div>
    <p class="tagline">Stay Consistent with RT in Your Pocket!</p>
  </section>

  <section class="post" style="left:27px; top:791px;">
    <div class="portrait" role="img" aria-label="Smiling coach in black outfit, hand on hip"></div>
    <div class="copy" style="top:30px;">
      <p class="lead tight">Eat the<br>food<br>you love.</p>
      <p class="punch">Stay<br>account-<br>able<br>every<br>day.</p>
    </div>
    <p class="tagline">Stay Consistent with RT in Your Pocket!</p>
  </section>

  <section class="post" style="left:319px; top:791px;">
    <div class="portrait" role="img" aria-label="Smiling coach in black outfit, hand on hip"></div>
    <div class="copy" style="top:86px; left:19px;">
      <p class="lead">One<br>Bad Meal</p>
      <p class="punch">Doesn&#39;t<br>mean<br>you<br>failed</p>
    </div>
    <p class="tagline" style="left:19px;">Stay Consistent with RT in Your Pocket!</p>
  </section>

</main>
</body>
</html>
```